YouTube Thumbnail for Educational Video About WW2

Please design a bespoke thumbnail for a YouTube video with the following title:
"Nobody Expected Such An Odd Clash Ever"
The video is about the battle for Castle Vornholm, which was a small battle that happened during WW2, in which the Germans fought against themselves for control of Castle Vornholm.
The thumbnail should be 1920x1080 pixels

```html
<!DOCTYPE html>
<html lang="en">
<head>
<meta charset="utf-8">
<title>Nobody Expected Such An Odd Clash Ever — Thumbnail</title>
<link href="https://fonts.googleapis.com/css2?family=Bebas+Neue&display=swap" rel="stylesheet">
<style>
  :root {
    --page-bg: #e6e6e6;
    --sky-dark: #3a3a37;
    --smoke-mid: #6b6660;
    --earth-warm: #6a4127;
    --earth-deep: #3b2414;
    --peach: #f1b48f;
    --band-brown: #a87a5c;
    --title-white: #ffffff;
    --rule-grey: #a9adb3;
    --star-blue: #a8b4c6;
  }
  * { margin: 0; padding: 0; box-sizing: border-box; }
  html, body {
    width: 909px;
    height: 1200px;
    overflow: hidden;
    background: var(--page-bg);
  }
  .canvas {
    position: relative;
    width: 909px;
    height: 1200px;
  }
  .thumbnail {
    position: absolute;
    left: 24px;
    top: 358px;
    width: 861px;
    height: 484px;
    overflow: hidden;
    box-shadow: 0 6px 14px rgba(0,0,0,0.35);
  }
  .battle-scene {
    position: absolute;
    inset: 0;
    background:
      radial-gradient(ellipse at 50% 45%, rgba(150,140,128,0.55) 0%, rgba(0,0,0,0) 60%),
      linear-gradient(180deg, var(--sky-dark) 0%, var(--smoke-mid) 40%, var(--earth-warm) 78%, var(--earth-deep) 100%);
  }
  .headline {
    position: absolute;
    left: 0;
    right: 0;
    top: 102px;
    display: flex;
    flex-direction: column;
    align-items: center;
    font-family: "Bebas Neue", "Arial Narrow", sans-serif;
    text-transform: uppercase;
    line-height: 1;
  }
  .headline-lead {
    display: flex;
    align-items: center;
    gap: 22px;
    color: var(--peach);
    font-size: 70px;
    letter-spacing: 1px;
  }
  .headline-rule {
    width: 128px;
    height: 3px;
    background: var(--rule-grey);
  }
  .headline-band {
    margin-top: 2px;
    padding: 4px 12px 0;
    background: var(--band-brown);
    border-radius: 6px;
    color: var(--title-white);
    font-size: 70px;
    letter-spacing: 1px;
  }
  .headline-close {
    display: flex;
    align-items: center;
    gap: 22px;
    margin-top: 6px;
    color: var(--peach);
    font-size: 112px;
    letter-spacing: 2px;
  }
  .star { width: 44px; height: 44px; }
  .star path { fill: var(--star-blue); }
</style>
</head>
<body>
  <main class="canvas">
    <section class="thumbnail">
      <div class="battle-scene" role="img" aria-label="Smoky black and white battle scene: a stone castle tower on the left, bomber planes across the sky and tanks with soldiers advancing through dust and embers"></div>
      <div class="headline">
        <div class="headline-lead">
          <span class="headline-rule"></span>
          <span>Nobody Expected</span>
          <span class="headline-rule"></span>
        </div>
        <div class="headline-band">Such An Odd Clash</div>
        <div class="headline-close">
          <svg class="star" viewBox="0 0 24 24" aria-hidden="true"><path d="M12 1.5l3.1 6.9 7.4.7-5.6 5 1.7 7.4L12 17.6l-6.6 3.9 1.7-7.4-5.6-5 7.4-.7z"/></svg>
          <span>Ever</span>
          <svg class="star" viewBox="0 0 24 24" aria-hidden="true"><path d="M12 1.5l3.1 6.9 7.4.7-5.6 5 1.7 7.4L12 17.6l-6.6 3.9 1.7-7.4-5.6-5 7.4-.7z"/></svg>
        </div>
      </div>
    </section>
  </main>
</body>
</html>
```